Wren of Fabrics relaunch: brand, logo and website redesign

Wren of Fabrics www.wrenoffabrics.com is relaunching to focus on empowering style advice, e books and courses.
We need a new logo, brand identity and website which reflects this change.
The structure of the site and pages have been completed http://dev1.wrenoffabrics.com/
but we need to update the brand look and feel
Please read the full brief, uploaded, before submitting your designs.

Target Market(s)

Women, primarily aged 28-45, English speaking USA and UK
Ambitious and determined. Looking for solutions. Open to self-improvement.
Maybe not as confident with style and body image as other parts of their life.

Logo Text

Brand name Wren of Fabrics Strapline version 1: Unlock your personal best Strapline version 2: Unlock better Logo/graphical icon for use with/without text

Number of Pages Required

3 page

Font styles to use
Sans Serif

Requirements
Must have
• 1. Web designs for home page, a channel page and advice page (see attached brief)
Web designs must be consistent with new website design navigation, and page structure http://dev1.wrenoffabrics.com/
2. Web style guide to include colour palettes/system; web fonts, icons, illustrations and guidelines/examples free stock photography. see Mindmap upload for example of colour pallette we like.
Nice to have
• Ebook front covers
Quiz promotions
Course promotions
Other web pages
Social media pages eg Pagebook, Snapgrid,Chirpline
Should not have
• Paid photography or photos where don’t have the rights

```html
<!DOCTYPE html>
<html lang="en">
<head>
<meta charset="utf-8">
<title>Wren of Fabrics – Quizzes</title>
<link rel="stylesheet" href="https://fonts.googleapis.com/css2?family=Marcellus&family=Figtree:wght@400;500;600&display=swap">
<style>
:root{
  --navy:#1b2550;
  --pink:#e8459f;
  --orange:#fd8530;
  --gold:#d9925a;
  --wash:#f7f8fb;
  --white:#ffffff;
  --text:#1f2540;
  --teal:#1ec6c6;
}
*{margin:0;padding:0;box-sizing:border-box}
html,body{width:1200px;height:2281px;overflow:hidden;background:var(--white)}
body{position:relative;font-family:"Figtree",sans-serif;color:var(--text)}
.abs{position:absolute}
.hero-band{left:0;top:0;width:1200px;height:585px;background:var(--wash)}
.footer-band{left:0;top:1839px;width:1200px;height:442px;background:var(--wash)}
.brand{font-family:"Marcellus",serif;color:var(--gold);font-size:21px;letter-spacing:.5px;white-space:nowrap}
.nav{top:80px;font-size:14px;color:var(--navy)}
.cart{left:1069px;top:69px;width:42px;height:42px;border-radius:50%;background:var(--navy)}
.cart-count{left:1096px;top:64px;width:14px;height:14px;border-radius:50%;background:var(--orange);color:#fff;font-size:8px;text-align:center;line-height:14px}
.eyebrow{left:89px;top:250px;font-family:"Marcellus",serif;font-size:24px;color:var(--navy)}
.page-title{left:88px;top:284px;font-family:"Marcellus",serif;font-size:73px;line-height:1;font-weight:400;color:var(--pink)}
.ornament-slot{left:940px;top:280px;width:140px;height:76px;background:var(--wash)}
.photo{background:linear-gradient(120deg,#2f5f8e 0%,#3d6f9c 28%,#d9cfc8 45%,#e8e0da 70%,#f2efec 100%)}
.hero-photo{left:88px;top:445px;width:1025px;height:342px}
.badge{left:140px;top:497px;width:174px;height:55px;background:var(--pink);color:#fff;font-size:11px;font-weight:600;display:flex;align-items:center;padding-left:30px;gap:12px}
.badge-ring{width:26px;height:26px;border:1px solid rgba(255,255,255,.7);border-radius:50%}
.h-xl{font-family:"Marcellus",serif;font-size:56px;font-weight:400;color:var(--navy);line-height:1}
.copy{font-size:13.5px;line-height:29px;color:var(--text)}
.btn{display:flex;align-items:center;justify-content:center;font-weight:500;color:#fff;background:var(--orange);text-decoration:none}
.btn-ghost{background:transparent;border:1px solid var(--orange);color:var(--orange)}
.card-photo{top:1250px;width:335px;height:209px}
.card-title{top:1500px;font-family:"Marcellus",serif;font-size:40px;font-weight:400;color:var(--navy);line-height:1}
.card-copy{top:1561px;width:320px}
.card-btn{top:1676px;width:142px;height:49px;font-size:12px}
.f-head{top:1950px;font-size:13px;font-weight:600;color:var(--navy)}
.f-list{list-style:none;font-size:13px;color:var(--navy)}
.f-list li{height:29.5px}
.pill{left:624px;top:2053px;width:191px;height:39px;background:#fff;border-radius:6px;display:flex;align-items:center;padding-left:14px;gap:8px;box-shadow:0 2px 8px rgba(0,0,0,.04)}
.pill-dot{width:14px;height:14px;border-radius:50%;background:var(--teal)}
.pill small{font-size:6px;color:var(--navy)}
.pill b{font-size:10px;letter-spacing:2px;color:var(--navy)}
.social{top:1996px;width:44px;height:44px;border-radius:50%;background:var(--navy)}
.social.alt{background:var(--orange);box-shadow:0 4px 10px rgba(253,133,48,.35)}
.legal{left:0;width:1200px;text-align:center;color:var(--navy)}
</style>
</head>
<body>
<div class="abs hero-band"></div>
<div class="abs footer-band"></div>

<header>
  <div class="abs brand" style="left:88px;top:89px">Wren of Fabrics</div>
  <nav>
    <span class="abs nav" style="left:549px">Advice</span>
    <span class="abs nav" style="left:625px">Courses</span>
    <span class="abs nav" style="left:710px">Quizzes</span>
    <span class="abs nav" style="left:793px">Ebooks</span>
    <span class="abs nav" style="left:872px">About</span>
    <span class="abs nav" style="left:944px">Blog</span>
  </nav>
  <svg class="abs" style="left:1022px;top:83px" width="14" height="14" viewBox="0 0 14 14" fill="none" stroke="#1b2550" stroke-width="1.4"><circle cx="5.5" cy="5.5" r="4"/><path d="M8.5 8.5l4.5 4.5"/></svg>
  <div class="abs cart"></div>
  <svg class="abs" style="left:1082px;top:81px" width="16" height="17" viewBox="0 0 16 17" fill="none" stroke="#fff" stroke-width="1.5"><rect x="2" y="5" width="12" height="11" rx="1"/><path d="M5 7V4a3 3 0 016 0v3"/></svg>
  <div class="abs cart-count">1</div>
</header>

<section>
  <div class="abs eyebrow">Discover your style</div>
  <h1 class="abs page-title">Quizz</h1>
  <div class="abs ornament-slot" role="img" aria-label="Hand-lettered note pointing to the featured quiz"></div>
  <div class="abs photo hero-photo" role="img" aria-label="Flat-lay of folded jeans, a knitted sweater and a white mug"></div>
  <div class="abs badge"><span class="badge-ring"></span>Featured Quizz</div>

  <h2 class="abs h-xl" style="left:88px;top:850px">Clothing Quiz</h2>
  <p class="abs copy" style="left:88px;top:938px;width:470px">Lorem ipsum dolor sit amet, consetetur sadipscing elitr, sed diam nonumy eirmod tempor invidunt ut labore et dolore magna aliquyam erat, sed diam voluptua. At vero eos et accusam et justo duo dolores et ea rebum.</p>
  <p class="abs copy" style="left:600px;top:938px;width:470px">Lorem ipsum dolor sit amet, consetetur sadipscing elitr, sed diam nonumy eirmod tempor invidunt ut labore et dolore magna aliquyam erat, sed diam voluptua. At vero eos et accusam et justo duo dolores et ea rebum.</p>
  <a class="abs btn" style="left:88px;top:1071px;width:184px;height:65px;font-size:15px">Start</a>
</section>

<section>
  <div class="abs card-photo" style="left:85px;background:linear-gradient(135deg,#c9a57a,#eef0f6 40%,#f3f3f6 70%,#d98a55)" role="img" aria-label="Flat-lay of accessories: leopard shoes, sunglasses, bracelets and a tan wallet"></div>
  <div class="abs card-photo" style="left:432px;background:linear-gradient(135deg,#b9c2cc,#f0c8d2 45%,#d8a9b9 70%,#7c6a80)" role="img" aria-label="Wedding rings resting on a pink bouquet"></div>
  <div class="abs card-photo" style="left:780px;background:linear-gradient(120deg,#8a5a3a,#c9926a 35%,#e7b494 65%,#f1d0bc)" role="img" aria-label="Close-up of a braid and a hand at the neckline"></div>

  <h3 class="abs card-title" style="left:85px">Style Quiz</h3>
  <h3 class="abs card-title" style="left:432px">Wedding Quiz</h3>
  <h3 class="abs card-title" style="left:780px">Neckline Quiz</h3>

  <p class="abs copy card-copy" style="left:85px">Take the fast and fun style quiz to discover your unique style DNA. Free guides to how to look your best and what to wear for your body shape and age.</p>
  <p class="abs copy card-copy" style="left:432px">Take the fast and fun style quiz to discover your unique style DNA. Free guides to how to look your best and what to wear for your body shape and age.</p>
  <p class="abs copy card-copy" style="left:780px">Take the fast and fun style quiz to discover your unique style DNA. Free guides to how to look your best and what to wear for your body shape and age.</p>

  <a class="abs btn card-btn" style="left:85px">Start</a>
  <a class="abs btn btn-ghost card-btn" style="left:432px">Start</a>
  <a class="abs btn btn-ghost card-btn" style="left:780px">Start</a>
</section>

<footer>
  <div class="abs brand" style="left:88px;top:1952px">Wren of Fabrics</div>

  <div class="abs f-head" style="left:375px">Navigation</div>
  <ul class="abs f-list" style="left:375px;top:1982px"><li>Home</li><li>Advice</li><li>About</li><li>Contact</li></ul>

  <div class="abs f-head" style="left:499px">Product</div>
  <ul class="abs f-list" style="left:499px;top:1981px"><li>Courses</li><li>Quizzes</li><li>Ebooks</li><li>Blog</li></ul>

  <div class="abs f-head" style="left:624px">Place</div>
  <ul class="abs f-list" style="left:624px;top:1981px;width:260px"><li>24 Harlow Lane, Greenfield QLD 4100</li><li>contact@wrenoffabrics.com</li></ul>
  <div class="abs pill"><span class="pill-dot"></span><small>Call us on</small><b>0500-417-268</b></div>

  <div class="abs f-head" style="left:895px">Social Media</div>
  <div class="abs social" style="left:895px" aria-label="Pagebook"></div>
  <div class="abs social alt" style="left:957px" aria-label="Snapgrid"></div>
  <div class="abs social" style="left:1013px" aria-label="Video channel"></div>

  <div class="abs legal" style="top:2215px;font-size:10.5px;display:flex;justify-content:center;align-items:center;gap:6px">
    <svg width="14" height="14" viewBox="0 0 14 14" fill="none" stroke="#1b2550" stroke-width="1.1"><circle cx="7" cy="7" r="6"/><path d="M9 5.2a2.6 2.6 0 100 3.6"/></svg>
    Wren of Fabrics Company - All Rights Reserved
  </div>
  <div class="abs legal" style="top:2236px;font-size:7.5px">Terms &amp; Conditions | Privacy Policy | | Contact Us</div>
</footer>
</body>
</html>
```